Personal Chef Needs a Good Web Design

Hi everyone!
My name is Leo, I work as a private chef for last 10 years, traveling all around the world and cooking in private megayacht and villas.
I'm about to settle down in my hometown in Europe for a while. And therefore I need a website that will show my story, pics and recipes, nutritional advices and of course offer a Personal and Private Chef services( working for 4-5 families and bringing delicious food to their house).
My clients are extremely rich folks, but usually are down to earth ones.
I believe, the web site should be focused on attention to:
-VIP person's wife( as she is usually responsible for food for family) and be simple.
-to famous people agents and be on high level.

There will be about 10 different menus and 6 different service offers

--UPDATE--
Logo Design:
+My thoughts are- printed structure of the vegetable or fruit on a white font. Like you slice the buffalo tomato, put it in red paint and print it on the edge of the page. See attached files named logo. Can be any nice structured thing, like tomato, lemon, red cabbage etc.
+Classic logos with chef's hat or knives are good too.
+Need to have the space for me to add the name( the fonts can be provided)

Target Market(s)

Private person. 80% Russian clients.

Industry/Entity Type

Cooking

Coding

Coded - Design and coding required

Number of Pages Required

3 page

Requirements
Must have
• Contact form/ Request back call/ Schedule a free consultation
Nice to have
• The client will need to choose straight ahead from the range of services I offer, like:
• -Private Chef( cooking only for the client)
• -Personal Chef( cooking for around 5 clients, bringing the ready to be heated food to their door)
• -Romantic dinner for two
• -Professional Sommelier service
• -Build your kitchen( offering design, equipment and that will fit your requirements)
• -Other( flowers, waiters, barista, equipment rental)
• So this column should go right after the introduction/aboutme part and will lead to separate pages with how-it-works thing for each.

```html
<!DOCTYPE html>
<html lang="en">
<head>
<meta charset="utf-8">
<title>Leo Varga Kitchen · How It Works</title>
<link rel="stylesheet" href="https://fonts.googleapis.com/css2?family=Nunito+Sans:wght@700&family=Open+Sans:wght@400&display=swap">
<style>
:root{
  --accent:#d9944a;
  --ink:#2b2b2b;
  --body:#5a5a5a;
  --rule:#d6d6d6;
  --ring:#8a8a8a;
  --muted:#a3a3a3;
  --bg:#ffffff;
}
*{margin:0;padding:0;box-sizing:border-box}
html,body{width:1200px;height:1104px;overflow:hidden;background:var(--bg)}
body{position:relative;font-family:"Open Sans",Arial,sans-serif;color:var(--body)}
.site-header{position:absolute;left:0;top:0;width:1200px;height:82px;border-bottom:1px solid var(--rule)}
.brand{position:absolute;left:97px;top:29px;font-family:"Open Sans",Arial,sans-serif;font-weight:400;font-size:21px;letter-spacing:.2px;color:var(--ink)}
.menu-toggle{position:absolute;left:1067px;top:24px;width:35px;height:35px;border:1px solid var(--ring);border-radius:50%}
.menu-toggle span{position:absolute;left:11px;width:12px;height:2px;background:var(--accent)}
.section-title{position:absolute;left:0;top:138px;width:1200px;text-align:center;font-family:"Nunito Sans",Helvetica,sans-serif;font-weight:700;font-size:31px;color:var(--ink);letter-spacing:.2px}
.timeline-line{position:absolute;left:600px;top:347px;width:1px;height:491px;background:var(--ring)}
.step-icon{position:absolute;width:107px;height:107px;margin-left:-53.5px;margin-top:-53.5px;left:600px;border:1px solid var(--ring);border-radius:50%;background:var(--bg)}
.step-icon .disc{position:absolute;left:6px;top:6px;width:93px;height:93px;border-radius:50%;background:var(--accent);display:flex;align-items:center;justify-content:center}
.step{position:absolute;width:410px}
.step h2{font-family:"Nunito Sans",Helvetica,sans-serif;font-weight:700;font-size:18px;color:var(--ink);margin-bottom:18px}
.step p{font-size:12.2px;line-height:22.3px}
.step.left{left:97px}
.step.right{left:703px;width:410px}
.step.right p{letter-spacing:-.1px}
.footer-band{position:absolute;left:0;top:1020px;width:1200px;height:5px;background:var(--accent)}
.copyright{position:absolute;left:98px;top:1056px;font-size:12.2px;color:var(--body)}
.social{position:absolute;top:1052px;width:26px;height:26px;border-radius:4px;background:var(--muted)}
</style>
</head>
<body>
<header class="site-header">
  <div class="brand">Leo Varga Kitchen</div>
  <div class="menu-toggle" aria-label="Menu">
    <span style="top:12px"></span><span style="top:16px"></span><span style="top:20px"></span>
  </div>
</header>

<h1 class="section-title">HOW IT WORKS</h1>

<div class="timeline-line"></div>

<div class="step-icon" style="top:293px"><div class="disc">
  <svg width="58" height="46" viewBox="0 0 58 46" fill="none" stroke="#fff" stroke-width="4" stroke-linejoin="round">
    <ellipse cx="22" cy="17" rx="18" ry="13"/>
    <path d="M10 27 L6 36 L17 29"/>
    <path d="M42 12 C52 15 56 22 52 30 L56 40 L44 34 C36 36 28 34 24 30"/>
  </svg>
</div></div>

<div class="step-icon" style="top:492px"><div class="disc">
  <svg width="48" height="50" viewBox="0 0 48 50" fill="#fff">
    <rect x="2" y="6" width="44" height="42" rx="4"/>
    <rect x="10" y="0" width="5" height="12" rx="2"/>
    <rect x="33" y="0" width="5" height="12" rx="2"/>
    <g fill="#d9944a">
      <rect x="7" y="17" width="7" height="6"/><rect x="16" y="17" width="7" height="6"/><rect x="25" y="17" width="7" height="6"/><rect x="34" y="17" width="7" height="6"/>
      <rect x="7" y="26" width="7" height="6"/><rect x="16" y="26" width="7" height="6"/><rect x="25" y="26" width="7" height="6"/><rect x="34" y="26" width="7" height="6"/>
      <rect x="7" y="35" width="7" height="6"/><rect x="16" y="35" width="7" height="6"/><rect x="25" y="35" width="7" height="6"/><rect x="34" y="35" width="7" height="6"/>
    </g>
  </svg>
</div></div>

<div class="step-icon" style="top:690px"><div class="disc">
  <svg width="56" height="46" viewBox="0 0 56 46" fill="#fff">
    <rect x="20" y="2" width="34" height="30" rx="2"/>
    <path d="M2 32 L2 22 L10 12 L20 12 L20 32 Z"/>
    <path d="M7 21 L11 16 L16 16 L16 21 Z" fill="#d9944a"/>
    <circle cx="12" cy="36" r="7" stroke="#d9944a" stroke-width="3"/>
    <circle cx="43" cy="36" r="7" stroke="#d9944a" stroke-width="3"/>
  </svg>
</div></div>

<div class="step-icon" style="top:891px"><div class="disc">
  <svg width="72" height="48" viewBox="0 0 72 48" fill="#fff">
    <circle cx="8" cy="8" r="2"/><circle cx="14" cy="12" r="2"/><circle cx="22" cy="9" r="2.5"/>
    <path d="M2 18 L40 18 C40 28 32 34 21 34 C10 34 2 28 2 18 Z"/>
    <rect x="38" y="16" width="32" height="4" rx="2"/>
    <path d="M18 46 L14 46 L16 38 Z M24 46 L20 46 L22 38 Z M30 46 L26 46 L28 38 Z"/>
    <rect x="12" y="44" width="20" height="3"/>
  </svg>
</div></div>

<section class="step left" style="top:240px">
  <h2>STEP 1</h2>
  <p>Our first consultation will be in your home. We will discuss any food preferences you may have, as well as any allergy or dietary needs. At this time we will also discus what kind of meals you like, from meat and potatoes to all organic, vegan and vegetarian meals or international cuisine like Italian or Mexican .</p>
</section>

<section class="step right" style="top:439px">
  <h2>STEP 2</h2>
  <p style="line-height:15.5px">If you have concerns about your diet we can work with any restrictions you have.</p>
</section>

<section class="step left" style="top:637px">
  <h2>STEP 3</h2>
  <p>On your scheduled cook date&nbsp; We will prepare your meals in our commercial kitchen and drop them off to you at your convenience. Your meals will be chilled, packaged, labeled and stored in your refrigerator or freezer with easy instructions for heating. Meals can be packaged in single servings or family style.</p>
</section>

<section class="step right" style="top:838px">
  <h2>STEP 4</h2>
  <p>All meals will have special heating instructions which most only require you heating it up in the oven.</p>
</section>

<div class="footer-band"></div>
<footer>
  <p class="copyright">Copyrights © 2016, Leo Varga Kitchen . All Rights Reserved.</p>
  <span class="social" style="left:954px" aria-label="Social link"></span>
  <span class="social" style="left:994px" aria-label="Social link"></span>
  <span class="social" style="left:1035px" aria-label="Social link"></span>
  <span class="social" style="left:1075px" aria-label="Social link"></span>
</footer>
</body>
</html>
```